AGP letterhead

We need a letterhead design for our new company based in Los Angeles called "Amber Gate Pictures". We develop film and television projects. We work with investors, financiers, film production companies, film distribution and sales companies as well as studios. We would like to incorporate our logo (see attached) but make the letterhead simple and elegant. We need to include: logo, company address, phone number and company website.
Updates

Hello designers, Thanks for your submissions. For our letterhead, we are looking for something more simple and elegant. No heavy bars or lines. Make it feel light and clean. Not a lot of ink on the page. Use the logo and contact info but think "clean", "streamlined" and mostly white paper. Looking forward to seeing more... thanks! Amber Gate Pictures team

Target Market(s)

Studio executives, talent agents and agencies, financiers, investors.

Industry/Entity Type

It Company

Requirements
Must have
• Amber Gate Pictures logo (see attached). Logo may be cropped and altered appropriately for elegant letterhead design.
• Please include:
• COMPANY ADDRESS:
• Tolvane Arts Park
• 2850 Delmore Street
• Crest Hall, 2nd Floor
• Larkmont Shores, CA 91802
• COMPANY WEBSITE:
• www.ambergatepicturesco.example
• COMPANY PHONE NUMBER:
• 555-604-2187

```html
<!DOCTYPE html>
<html lang="en">
<head>
<meta charset="utf-8">
<title>Amber Gate Pictures Letterhead</title>
<link rel="stylesheet" href="https://fonts.googleapis.com/css2?family=PT+Sans:wght@400;700&display=swap">
<style>
  :root {
    --paper: #ffffff;
    --paper-shade: #f6f7f8;
    --ink: #555a5e;
    --rule: #9a9ea2;
    --brand-dark: #0d3441;
    --brand-blue: #1aa3d8;
    --swoosh: #00aeef;
    --footer-grey: #d3d5d7;
  }
  html, body {
    margin: 0;
    padding: 0;
    width: 950px;
    height: 1200px;
    overflow: hidden;
    background: var(--paper);
  }
  .letterhead {
    position: relative;
    width: 950px;
    height: 1200px;
    background: linear-gradient(160deg, var(--paper) 40%, var(--paper-shade) 100%);
    font-family: "PT Sans", Arial, sans-serif;
    color: var(--ink);
    overflow: hidden;
  }
  .brand {
    position: absolute;
    left: 58px;
    top: 45px;
    width: 240px;
    display: flex;
    flex-direction: column;
    align-items: center;
  }
  .brand-mark {
    width: 140px;
    height: 140px;
    border-radius: 50%;
    background: var(--brand-dark);
  }
  .brand-name {
    margin-top: 14px;
    font-size: 22px;
    font-weight: 700;
    letter-spacing: 1px;
    color: var(--brand-blue);
    white-space: nowrap;
  }
  .address {
    position: absolute;
    left: 466px;
    top: 78px;
    padding-left: 17px;
    border-left: 1px solid var(--rule);
    font-size: 17px;
    font-style: normal;
    font-weight: 400;
    line-height: 35px;
  }
  .address p { margin: 0; white-space: nowrap; }
  .footer-wave {
    position: absolute;
    left: 0;
    bottom: 0;
    width: 950px;
    height: 112px;
  }
  .contact {
    position: absolute;
    left: 38px;
    bottom: 10px;
    font-size: 17px;
    line-height: 25px;
  }
  .contact-line {
    display: flex;
    align-items: center;
    gap: 6px;
  }
  .contact-line svg { width: 14px; height: 14px; }
</style>
</head>
<body>
<main class="letterhead">
  <header>
    <div class="brand">
      <div class="brand-mark"></div>
      <div class="brand-name">Amber Gate Pictures</div>
    </div>
    <address class="address">
      <p>Tolvane Arts Park 2850 Delmore Street Crest Hall,</p>
      <p>2nd Floor Larkmont Shores, CA 91802</p>
    </address>
  </header>

  <footer>
    <svg class="footer-wave" viewBox="0 0 950 112" preserveAspectRatio="none" aria-hidden="true">
      <path d="M0,46 C240,26 440,42 600,74 C760,100 860,84 950,58 L950,112 L0,112 Z" fill="var(--footer-grey)"/>
      <path d="M0,14 C250,-4 450,30 570,58 C440,40 250,28 0,34 Z" fill="var(--swoosh)"/>
      <path d="M560,66 C750,84 880,54 950,28 L950,44 C860,74 740,88 560,66 Z" fill="var(--swoosh)"/>
    </svg>
    <div class="contact">
      <div class="contact-line">
        <svg viewBox="0 0 16 16" aria-hidden="true"><circle cx="8" cy="8" r="7" fill="none" stroke="var(--ink)" stroke-width="1"/><path d="M5.5,4.5 L7,6 L6,7.2 C6.6,8.4 7.6,9.4 8.8,10 L10,9 L11.5,10.5 L10.6,11.6 C7.6,11.2 4.8,8.4 4.4,5.4 Z" fill="var(--ink)"/></svg>
        <span>555-604-2187</span>
      </div>
      <div class="contact-line">
        <svg viewBox="0 0 16 16" aria-hidden="true"><g fill="none" stroke="var(--ink)" stroke-width="1"><circle cx="8" cy="8" r="7"/><ellipse cx="8" cy="8" rx="3" ry="7"/><path d="M1,8 H15 M2.5,4.5 H13.5 M2.5,11.5 H13.5"/></g></svg>
        <span>www.ambergatepicturesco.example</span>
      </div>
    </div>
  </footer>
</main>
</body>
</html>
```